Property restoration company needs 'Appreciation Packet' to send customers

Need 3 items designed.
- a branded 'Thank You' greeting card. 4"x6" fold over style. Should look professional and match our brand identity. I would like to be able to get these printed with a specific message inside and also as blank-inside cards to hand write custom messages into.

Business is owned by a father and son. The thank you message in the card will be signed from both of us. I would like to add our pictures inside the card under the message to give it a personal feeling.

- a card requesting google reviews with a QR code linked to review form. Business card sized when printed. Front & Back printing.

- an information card explaining that we pay referral fees. Business card sized. Front & Back printing

```html
<!DOCTYPE html>
<html lang="en">
<head>
<meta charset="utf-8">
<title>Harbor Restore – Thank You Card</title>
<link href="https://fonts.googleapis.com/css2?family=Poppins:wght@400;500;600;700&display=swap" rel="stylesheet">
<style>
  :root {
    --backdrop: #c8c8c8;
    --brand-blue: #00a8dc;
    --bright-blue: #12aee3;
    --charcoal: #262626;
    --ink: #1f1f1f;
    --white: #ffffff;
    --mist: #d9f2f8;
    --mist-deep: #a9e2ef;
    --ring: #7fb8ca;
  }
  * { box-sizing: border-box; margin: 0; padding: 0; }
  html, body { width: 798px; height: 1200px; overflow: hidden; }
  body {
    background: var(--backdrop);
    font-family: "Poppins", sans-serif;
    position: relative;
  }
  .card {
    position: absolute;
    left: 68px;
    width: 658px;
    height: 493px;
    overflow: hidden;
    box-shadow: 0 10px 22px rgba(0,0,0,0.28);
    background: var(--white);
  }
  .card--outside { top: 81px; }
  .card--inside { top: 629px; }

  .watercolor {
    position: absolute;
    top: 0; right: 0;
    width: 329px; height: 100%;
    background:
      radial-gradient(ellipse 60% 40% at 90% 10%, var(--mist-deep), transparent 70%),
      radial-gradient(ellipse 50% 45% at 10% 80%, var(--mist-deep), transparent 70%),
      radial-gradient(ellipse 70% 60% at 40% 45%, var(--mist), transparent 75%),
      linear-gradient(160deg, #f4fbfd 0%, #e3f5fa 50%, #d2eff7 100%);
  }

  /* Outside: back panel */
  .back-panel {
    position: absolute; left: 0; top: 0;
    width: 329px; height: 100%;
    background: var(--charcoal);
    color: var(--white);
    text-align: center;
  }
  .brand-name {
    display: flex; align-items: center; gap: 6px;
    font-weight: 700; color: var(--bright-blue);
    line-height: 0.95; text-transform: uppercase;
  }
  .brand-name__dot {
    border-radius: 50%;
    border: 3px solid var(--bright-blue);
    flex: none;
  }
  .back-panel .brand-name {
    position: absolute; left: 90px; top: 262px; font-size: 24px;
  }
  .back-panel .brand-name__dot { width: 40px; height: 40px; }
  .contact-icons {
    position: absolute; top: 331px; left: 0; width: 100%;
    display: flex; justify-content: center; gap: 2px;
  }
  .contact-icons span {
    width: 15px; height: 15px; border-radius: 50%;
    background: var(--bright-blue);
    display: flex; align-items: center; justify-content: center;
  }
  .contact-line {
    position: absolute; left: 0; width: 100%;
    font-size: 11.5px; line-height: 14px;
  }
  .contact-line--web { font-weight: 600; font-size: 12px; }
  .contact-line--web em { font-style: normal; color: var(--bright-blue); }

  /* Outside: front panel */
  .front-panel { position: absolute; left: 329px; top: 0; width: 329px; height: 100%; }
  .front-panel .brand-name { position: absolute; left: 48px; top: 85px; font-size: 30px; }
  .front-panel .brand-name__dot { width: 48px; height: 48px; }
  .accent-bar { position: absolute; background: var(--bright-blue); }
  .accent-bar--top { left: 242px; top: 0; width: 12px; height: 270px; }
  .accent-bar--down { left: 63px; top: 215px; width: 12px; height: 278px; }
  .headline {
    position: absolute; font-weight: 600; letter-spacing: -2px; line-height: 1;
  }
  .headline--thank { left: 48px; top: 196px; font-size: 80px; color: var(--bright-blue); }
  .headline--you { left: 94px; top: 248px; font-size: 80px; color: var(--charcoal); }
  .front-web {
    position: absolute; left: 0; width: 100%; top: 430px;
    text-align: right; padding-right: 55px;
    font-size: 12px; font-weight: 600; color: var(--ink);
  }

  /* Inside */
  .message-panel {
    position: absolute; left: 0; top: 0;
    width: 329px; height: 359px;
    background: var(--brand-blue);
  }
  .frame { position: absolute; left: 0; top: 0; }
  .inside-thank {
    position: absolute; left: 114px; top: 48px;
    color: var(--white); font-weight: 600; line-height: 0.85;
  }
  .inside-thank__word { position: absolute; font-size: 32px; letter-spacing: -1px; white-space: nowrap; }
  .inside-thank__word--thank { left: 0; top: 14px; }
  .inside-thank__word--you { left: 18px; top: 40px; color: var(--charcoal); }
  .inside-thank__bar { position: absolute; background: var(--white); width: 4px; }
  .message {
    position: absolute; left: 40px; top: 151px; width: 252px;
    text-align: center; color: var(--white);
    font-size: 11.3px; line-height: 13.7px;
  }
  .portrait-ring {
    position: absolute; left: 100px; top: 292px;
    width: 130px; height: 130px; border-radius: 50%;
    background: var(--ring);
    display: flex; align-items: center; justify-content: center;
  }
  .portrait {
    width: 112px; height: 112px; border-radius: 50%;
    background: radial-gradient(circle at 50% 60%, #9aa6ad 0%, #d9dee1 55%, #ffffff 75%);
  }
  .signature {
    position: absolute; top: 416px; width: 92px; height: 26px;
    border-bottom: 1px solid #7a7a7a;
  }
  .signature__mark {
    width: 70%; height: 14px; margin: 6px auto 0;
    background: linear-gradient(90deg, transparent, rgba(40,40,40,0.18), transparent);
  }
  .signature--left { left: 34px; }
  .signature--right { left: 219px; }
  .note-area {
    position: absolute; left: 367px; top: 41px;
    width: 254px; height: 400px; border-radius: 7px;
    background: var(--white);
    box-shadow: 0 1px 6px rgba(0,0,0,0.08);
  }
  .corner-badge {
    position: absolute; left: 570px; top: 410px;
    width: 92px; height: 92px; border-radius: 50%;
    background: var(--bright-blue);
  }
</style>
</head>
<body>

<section class="card card--outside">
  <div class="back-panel">
    <div class="brand-name"><span>Harbor<br>Restore</span><span class="brand-name__dot"></span></div>
    <div class="contact-icons" aria-hidden="true">
      <span><svg width="9" height="9" viewBox="0 0 24 24"><path fill="#fff" d="M6.6 10.8a15 15 0 0 0 6.6 6.6l2.2-2.2c.3-.3.7-.4 1-.2 1.1.4 2.3.6 3.6.6.6 0 1 .4 1 1V20c0 .6-.4 1-1 1A17 17 0 0 1 3 4c0-.6.4-1 1-1h3.5c.6 0 1 .4 1 1 0 1.3.2 2.5.6 3.6.1.3 0 .7-.2 1z"/></svg></span>
      <span><svg width="9" height="9" viewBox="0 0 24 24"><rect x="2" y="5" width="20" height="14" rx="2" fill="#fff"/><path d="M3 6l9 7 9-7" stroke="#12aee3" stroke-width="2" fill="none"/></svg></span>
      <span><svg width="9" height="9" viewBox="0 0 24 24"><path fill="#fff" d="M12 2a7 7 0 0 0-7 7c0 5 7 13 7 13s7-8 7-13a7 7 0 0 0-7-7zm0 9.5A2.5 2.5 0 1 1 12 6.5a2.5 2.5 0 0 1 0 5z"/></svg></span>
      <span><svg width="9" height="9" viewBox="0 0 24 24"><circle cx="12" cy="12" r="9" fill="none" stroke="#fff" stroke-width="2"/><path d="M3 12h18M12 3c3 3 3 15 0 18M12 3c-3 3-3 15 0 18" stroke="#fff" stroke-width="1.6" fill="none"/></svg></span>
    </div>
    <p class="contact-line" style="top:353px">555-014-2290</p>
    <p class="contact-line" style="top:373px">hello@harborrestore.com</p>
    <p class="contact-line" style="top:396px">240 Lakeview Rd #12<br>Brookfield, TX 75990</p>
    <p class="contact-line contact-line--web" style="top:431px">www.<em>harborrestore</em>.com</p>
  </div>

  <div class="front-panel">
    <div class="watercolor" style="width:100%"></div>
    <div class="brand-name"><span>Harbor<br>Restore</span><span class="brand-name__dot"></span></div>
    <div class="accent-bar accent-bar--top"></div>
    <div class="accent-bar accent-bar--down"></div>
    <h1 class="headline headline--thank">Thank</h1>
    <p class="headline headline--you">you</p>
    <p class="front-web">www.harborrestore.com</p>
  </div>
</section>

<section class="card card--inside">
  <div class="watercolor"></div>
  <div class="message-panel"></div>
  <svg class="frame" width="658" height="493" aria-hidden="true">
    <polyline points="21,359 21,21 329,21" fill="none" stroke="rgba(255,255,255,0.85)" stroke-width="1.4"/>
    <polyline points="329,21 637,21 637,473 21,473 21,373" fill="none" stroke="#12aee3" stroke-width="1.4"/>
  </svg>
  <div class="inside-thank">
    <span class="inside-thank__bar" style="left:6px;top:30px;height:51px"></span>
    <span class="inside-thank__bar" style="left:86px;top:0;height:52px"></span>
    <span class="inside-thank__word inside-thank__word--thank">Thank</span>
    <span class="inside-thank__word inside-thank__word--you">you</span>
  </div>
  <p class="message">It is a long established fact that a reader will be distracted by the readable content of a page when looking at its layout. The point of using Lorem Ipsum is that it has a more-or-less normal distribution of letters, as opposed to using 'Content here, content here', making it look like readable English.</p>
  <div class="portrait-ring">
    <div class="portrait" role="img" aria-label="Photo of the father and son owners standing with arms crossed"></div>
  </div>
  <div class="signature signature--left"><div class="signature__mark" role="img" aria-label="Handwritten signature of Ethan Cole"></div></div>
  <div class="signature signature--right"><div class="signature__mark" role="img" aria-label="Handwritten signature of Mark Cole"></div></div>
  <div class="note-area"></div>
  <div class="corner-badge"></div>
</section>

</body>
</html>
```